"Inkvale" printing shop

-The design must be based around the attached HPID (home page information design) called "Inkvale - HPID".

The table boxes are just for approximate placement of information – you DON'T have to box everything in and you can arrange these. All fonts used in the HPID are only examples - you can use any Google font you wish.

- Information only is in orange text. Copy to go on the design in black text. Some instructions are in the HPID. Please be creative!

-The design needs to be modern. Colours are to be consistent with their new logo or complement it. Keep it clean and simple, you don't need to use lots of colours. Use lots of white.

- images / icons for the site need to be relevant and high quality, but they must also be free images or icons. I have attached a few examples that could be used.

Width of content will be 1100 pixels when implemented as a web page. Header height (without nav bar) 150-200 pixels.

If your design is chosen the winning PSD file will have to be provided as follows…
1. Canvas size of 2000px x 2000px - 72ppi in Adobe Photoshop (CS5 compatible)
2. Width of content section is 1100px wide - centered in the canvas
3. Any button rollovers/hovers in the PSD as hidden layers.
4. All fonts used must be Google fonts.
5. You will need to supply the chosen home page plus one example page (example page as a style guide for how all other pages will look). Example page is only the header and navigational bar at the top, an empty sector in the middle with a column (190 px wide) which can be left or right aligned which means the main sector is 910 pixels wide, and then the footer at the bottom of the page

Checklist - http://pagebuildertally.example/

Examples of some websites that have great design... don't copy them please but they are similar in look to what we are after....
http://www.rookfenly.example/

Industry/Entity Type

Printing

Font styles to use
Serif
Sans Serif

Requirements
Should not have
• Drop shadows, comic sans font

```html
<!DOCTYPE html>
<html lang="en">
<head>
<meta charset="utf-8">
<title>Inkvale – Printing, Laminating and Photocopying</title>
<link rel="stylesheet" href="https://fonts.googleapis.com/css2?family=Open+Sans:wght@300;400;600;700&family=Courgette&display=swap">
<style>
:root{
  --brand:#c8415d;
  --brand-red:#c0283c;
  --navy:#263a8e;
  --ink:#111;
  --text:#555;
  --muted:#8a8a8a;
  --line:#d6d6d6;
  --teal:#1ea0b8;
  --green:#26a27c;
  --red:#dc4444;
  --yellow:#e3b92b;
  --orange:#e86a36;
  --purple:#b84cb8;
  --link:#f08a12;
  --footer:#efefef;
  --bar:#e2e2e2;
}
*{box-sizing:border-box;margin:0;padding:0}
html,body{width:1200px;height:2594px;overflow:hidden}
body{font-family:"Open Sans",Arial,sans-serif;color:var(--text);background:#fff;position:relative}
.abs{position:absolute}

/* header */
.site-header{position:absolute;left:0;top:0;width:1200px;height:86px;background:#fff}
.logo{left:99px;top:18px;display:flex;align-items:center;gap:8px}
.logo-mark{width:36px;height:36px;border-radius:50%;background:var(--navy)}
.logo-name{font-size:25px;font-weight:700;color:var(--navy);letter-spacing:-.5px}
.tagline{left:268px;top:16px;font-family:"Courgette",cursive;color:#8a8a8a;font-size:14px;line-height:22px}
.header-contact{left:842px;top:10px;font-size:12.5px;color:#8a8a8a;line-height:22px}
.header-contact h4{color:var(--brand-red);font-weight:700;font-size:13px}
.header-contact p{display:flex;align-items:center;gap:7px}

/* nav */
.main-nav{position:absolute;left:0;top:86px;width:1200px;height:44px;background:var(--brand);display:flex;align-items:center;justify-content:space-between;padding:0 100px 0 107px}
.main-nav a{color:#fff;text-decoration:none;font-size:12px;white-space:nowrap}

/* hero */
.hero{position:absolute;left:0;top:130px;width:1200px;height:463px;
  background:linear-gradient(100deg,#d9d3c4 0%,#cfc6b2 25%,#c04f7a 38%,#e0a030 48%,#bdb8ae 62%,#b9b2a6 80%,#a9a398 100%)}
.hero-caption{position:absolute;left:99px;background:rgba(20,20,20,.9);color:#fff;font-weight:700;font-size:16.5px;letter-spacing:.4px;height:48px;display:flex;align-items:center;padding:0 24px;white-space:nowrap}
.hero-arrow{position:absolute;top:352px;width:36px;height:36px;border-radius:50%;background:rgba(255,255,255,.45);display:flex;align-items:center;justify-content:center}

/* section heads */
.section-title{position:absolute;left:0;width:1200px;text-align:center;color:var(--ink);font-weight:700;font-size:24px;letter-spacing:.3px}
.section-sub{position:absolute;left:0;width:1200px;text-align:center;color:#9a9a9a;font-weight:300;font-size:17px;letter-spacing:.2px}

/* feature tiles */
.feature{position:absolute;width:300px;text-align:center}
.feature-icon{width:121px;height:121px;margin:0 auto;display:flex;align-items:center;justify-content:center}
.feature h3{margin-top:20px;color:var(--ink);font-size:13.5px;font-weight:700;letter-spacing:.3px}
.feature p{margin-top:8px;font-size:12px;line-height:21.5px;color:var(--muted)}

/* services */
.services{position:absolute;left:0;top:1366px;width:1200px;height:600px;
  background:radial-gradient(ellipse at 55% 55%,#f6f6f6 0%,#e6e6e6 55%,#dcdcdc 100%)}
.service{position:absolute;width:400px}
.service-icon{position:absolute;left:-55px;top:-4px;width:52px;height:52px;border-radius:50%;display:flex;align-items:center;justify-content:center}
.service h3{font-size:17px;font-weight:400;color:#222}
.service p{margin-top:8px;font-size:12px;line-height:22px;color:#555}
.service a{display:flex;align-items:center;gap:7px;margin-top:6px;color:var(--link);font-size:12px;text-decoration:none}

/* quote */
.quote-title{left:99px;top:2030px;color:var(--ink);font-size:24px;font-weight:700}
.quote-text{left:99px;top:2078px;width:395px;font-size:12px;line-height:24px;color:#444}
.field{position:absolute;border:1px solid var(--line);background:#fff;font-size:12px;color:#666;padding:8px 12px;height:36px}
.submit{position:absolute;left:814px;top:2142px;width:279px;height:40px;background:var(--navy);color:#fff;font-weight:700;font-size:13px;display:flex;align-items:center;justify-content:center;letter-spacing:.3px}

/* footer */
.site-footer{position:absolute;left:0;top:2270px;width:1200px;height:275px;background:var(--footer)}
.partner-badge{position:absolute;left:111px;width:152px;height:80px;border:1px solid #d0d0d0;background:#f7f7f7;display:flex;align-items:center;justify-content:center}
.footer-col{position:absolute;top:2316px;font-size:11px;color:#555;line-height:22px;text-transform:uppercase}
.footer-col h4{color:var(--navy);font-size:13.5px;font-weight:700;margin-bottom:6px}
.footer-col li{list-style:none}
.contact-line{display:flex;align-items:center;gap:10px}
.social li{display:flex;align-items:center;gap:8px;margin-bottom:13px;line-height:22px}
.social-square{width:24px;height:24px;border:1px solid #999;background:#fff}
.bottom-bar{position:absolute;left:0;top:2545px;width:1200px;height:49px;background:var(--bar);display:flex;align-items:center;justify-content:center;font-size:11px;color:#555}
</style>
</head>
<body>

<header class="site-header">
  <div class="abs logo"><span class="logo-mark"></span><span class="logo-name">Inkvale</span></div>
  <div class="abs tagline">Duplication is our vocation<br>Professional photocopying - digital &amp; film processing, design and printing</div>
  <div class="abs header-contact">
    <h4>CONTACT</h4>
    <p><svg width="9" height="12" viewBox="0 0 9 12"><path d="M4.5 0A4.5 4.5 0 0 0 0 4.5C0 8 4.5 12 4.5 12S9 8 9 4.5A4.5 4.5 0 0 0 4.5 0zm0 6.3a1.8 1.8 0 1 1 0-3.6 1.8 1.8 0 0 1 0 3.6z" fill="#8a8a8a"/></svg>3/17 Harbour Lane - Fernbay - Tauranga</p>
    <p><svg width="10" height="10" viewBox="0 0 10 10"><path d="M2 0l2 2.5-1.2 1.2a6 6 0 0 0 3.5 3.5L7.5 6 10 8l-1.5 2C4 10 0 6 0 1.5z" fill="#8a8a8a"/></svg>07 555 0148,</p>
  </div>
</header>

<nav class="main-nav">
  <a href="#">Photocopying</a><a href="#">Printing</a><a href="#">laminating</a><a href="#">Business cards</a><a href="#">Typing services</a><a href="#">Film processing</a><a href="#">Photo printing</a><a href="#">Passport photos</a><a href="#">Image restoration</a><a href="#">Printer supplies</a>
</nav>

<section class="hero" role="img" aria-label="Smiling young woman in a grey hoodie spraying bursts of colourful paint across a pale wall">
  <div class="hero-caption" style="top:259px">DIGITAL PRINTING, LAMINATING</div>
  <div class="hero-caption" style="top:316px">AND PHOTOCOPYING SERVICES THROUGHOUT TAURANGA</div>
  <div class="hero-arrow" style="left:52px"><svg width="10" height="14" viewBox="0 0 10 14"><path d="M8 1 2 7l6 6" stroke="#fff" stroke-width="2.5" fill="none"/></svg></div>
  <div class="hero-arrow" style="left:1128px"><svg width="10" height="14" viewBox="0 0 10 14"><path d="m2 1 6 6-6 6" stroke="#fff" stroke-width="2.5" fill="none"/></svg></div>
</section>

<h2 class="section-title" style="top:641px">WELCOME TO INKVALE</h2>
<p class="section-sub" style="top:677px">DIGITAL PRINTING, LAMINATING AND PHOTOCOPYING SERVICES THROUGHOUT TAURANGA</p>

<div class="feature" style="left:90px;top:762px">
  <div class="feature-icon" style="background:var(--teal)"><svg width="52" height="44" viewBox="0 0 52 44"><rect x="2" y="8" width="48" height="34" rx="7" fill="#fff"/><rect x="17" y="2" width="18" height="10" rx="3" fill="#fff"/><circle cx="26" cy="25" r="11" fill="var(--teal)"/><circle cx="26" cy="25" r="7" fill="#fff"/></svg></div>
  <h3>PHOTOCOPYING</h3>
  <p>Lorem Ipsum has been the industry's<br>standard dummy text ever since the 1500s, when<br>an unknown printer took a galley of type and<br>scrambled it to make</p>
</div>
<div class="feature" style="left:450px;top:762px">
  <div class="feature-icon" style="background:var(--green)"><svg width="56" height="56" viewBox="0 0 56 56"><rect x="5" y="8" width="46" height="44" rx="3" fill="none" stroke="#fff" stroke-width="4"/><g stroke="#fff" stroke-width="3"><path d="M14 3v9M22 3v9M30 3v9M38 3v9M46 3v9"/><path d="M14 24h28M14 32h28M14 40h28"/></g></svg></div>
  <h3>LAMINATING &amp; BINDING</h3>
  <p>Lorem Ipsum has been the industry's<br>standard dummy text ever since the 1500s, when<br>an unknown printer took a galley of type and<br>scrambled it to make</p>
</div>
<div class="feature" style="left:811px;top:762px">
  <div class="feature-icon" style="background:var(--red)"><svg width="52" height="50" viewBox="0 0 52 50"><rect x="13" y="2" width="26" height="14" fill="#fff"/><rect x="2" y="18" width="48" height="20" rx="5" fill="#fff"/><rect x="13" y="30" width="26" height="18" fill="#fff" stroke="var(--red)" stroke-width="3"/><circle cx="42" cy="25" r="2.5" fill="var(--red)"/></svg></div>
  <h3>DIGITAL PRINTING</h3>
  <p>Lorem Ipsum has been the industry's<br>standard dummy text ever since the 1500s, when<br>an unknown printer took a galley of type and<br>scrambled it to make</p>
</div>

<div class="feature" style="left:90px;top:1055px">
  <div class="feature-icon" style="background:var(--yellow)"><svg width="56" height="46" viewBox="0 0 56 46"><rect x="3" y="3" width="50" height="40" rx="4" fill="none" stroke="#fff" stroke-width="4"/><path d="M15 3v40M41 3v40M15 23h26M3 13h12M3 23h12M3 33h12M41 13h12M41 23h12M41 33h12" stroke="#fff" stroke-width="3"/></svg></div>
  <h3>FILM PROCESSING</h3>
  <p>Lorem Ipsum has been the industry's<br>standard dummy text ever since the 1500s, when<br>an unknown printer took a galley of type and<br>scrambled it to make</p>
</div>
<div class="feature" style="left:450px;top:1055px">
  <div class="feature-icon" style="background:var(--orange)"><svg width="56" height="42" viewBox="0 0 56 42"><rect x="3" y="3" width="50" height="36" rx="4" fill="none" stroke="#fff" stroke-width="4"/><path d="M3 14h50" stroke="#fff" stroke-width="6"/><path d="M11 29h10M25 29h6" stroke="#fff" stroke-width="3"/></svg></div>
  <h3>BUSINESS CARDS</h3>
  <p>Lorem Ipsum has been the industry's<br>standard dummy text ever since the 1500s, when<br>an unknown printer took a galley of type and<br>scrambled it to make</p>
</div>
<div class="feature" style="left:811px;top:1055px">
  <div class="feature-icon" style="background:var(--purple)"><svg width="58" height="52" viewBox="0 0 58 52"><g fill="none" stroke="#fff" stroke-width="3.5" stroke-linejoin="round"><path d="M29 4 54 16 29 28 4 16z"/><path d="M4 25l25 12 25-12"/><path d="M4 34l25 12 25-12"/></g></svg></div>
  <h3>PHOTO PRINTING</h3>
  <p>Lorem Ipsum has been the industry's<br>standard dummy text ever since the 1500s, when<br>an unknown printer took a galley of type and<br>scrambled it to make</p>
</div>

<section class="services">
  <h2 class="section-title" style="top:62px">OUR SERVICES</h2>
  <p class="section-sub" style="top:98px">DIGITAL PRINTING, LAMINATING AND PHOTOCOPYING SERVICES THROUGHOUT TAURANGA</p>

  <div class="service" style="left:214px;top:181px">
    <div class="service-icon" style="background:var(--teal)"><svg width="20" height="16" viewBox="0 0 20 16"><rect x="1" y="1" width="18" height="14" fill="none" stroke="#fff" stroke-width="2"/><path d="M3 13l5-5 3 3 2-2 4 4z" fill="#fff"/></svg></div>
    <h3>Cost effective photocopying</h3>
    <p>No matter the quantity of photocopies you need or the size of your<br>copy - you can rely on us to provide a top quality service!</p>
    <a href="#">Click for Photocopying <svg width="12" height="12" viewBox="0 0 12 12"><circle cx="6" cy="6" r="6" fill="var(--link)"/><path d="m5 3 3 3-3 3" stroke="#fff" stroke-width="1.6" fill="none"/></svg></a>
  </div>
  <div class="service" style="left:728px;top:181px">
    <div class="service-icon" style="background:var(--green)"><svg width="20" height="14" viewBox="0 0 20 14"><rect x="3" y="1" width="14" height="9" fill="none" stroke="#fff" stroke-width="2"/><path d="M0 12h20" stroke="#fff" stroke-width="2.5"/></svg></div>
    <h3>Personal desktop publishing</h3>
    <p>From personalised brochures, posters and birthday and special occa-<br>sion cards to top quality, cheap business cards - you get it all!</p>
    <a href="#">Click for Desktop Publishing <svg width="12" height="12" viewBox="0 0 12 12"><circle cx="6" cy="6" r="6" fill="var(--link)"/><path d="m5 3 3 3-3 3" stroke="#fff" stroke-width="1.6" fill="none"/></svg></a>
  </div>

  <div class="service" style="left:214px;top:311px">
    <div class="service-icon" style="background:var(--red)"><svg width="20" height="18" viewBox="0 0 20 18"><rect x="5" y="1" width="10" height="5" fill="#fff"/><rect x="1" y="6" width="18" height="7" rx="2" fill="#fff"/><rect x="5" y="11" width="10" height="6" fill="#fff" stroke="var(--red)" stroke-width="1.5"/></svg></div>
    <h3>All digital format printing</h3>
    <p>Either email us your file or bring it into the store and we can get you<br>the print you need. All prints are to the highest quality.</p>
    <a href="#">Click for Digital Printing <svg width="12" height="12" viewBox="0 0 12 12"><circle cx="6" cy="6" r="6" fill="var(--link)"/><path d="m5 3 3 3-3 3" stroke="#fff" stroke-width="1.6" fill="none"/></svg></a>
  </div>
  <div class="service" style="left:728px;top:311px">
    <div class="service-icon" style="background:var(--yellow)"><svg width="20" height="16" viewBox="0 0 20 16"><rect x="1" y="1" width="18" height="14" fill="none" stroke="#fff" stroke-width="2"/><path d="M6 1v14M14 1v14M6 8h8" stroke="#fff" stroke-width="1.6"/></svg></div>
    <h3>Film photo processing</h3>
    <p>Bring in your film to the store and we will work with you to get the<br>best quality print for your purpose and needs. We work with it all!</p>
    <a href="#">Click for Photo Film Processing <svg width="12" height="12" viewBox="0 0 12 12"><circle cx="6" cy="6" r="6" fill="var(--link)"/><path d="m5 3 3 3-3 3" stroke="#fff" stroke-width="1.6" fill="none"/></svg></a>
  </div>

  <div class="service" style="left:214px;top:441px">
    <div class="service-icon" style="background:var(--orange)"><svg width="20" height="16" viewBox="0 0 20 16"><rect x="1" y="1" width="18" height="14" fill="none" stroke="#fff" stroke-width="2"/><path d="M4 5h12M4 8h12M4 11h12" stroke="#fff" stroke-width="1.5"/></svg></div>
    <h3>Laminating and binding</h3>
    <p>Create a professional image for your documents or books. Lamination<br>and binding also keeps your documents well protected!</p>
    <a href="#">Click for Lamination &amp; Binding <svg width="12" height="12" viewBox="0 0 12 12"><circle cx="6" cy="6" r="6" fill="var(--link)"/><path d="m5 3 3 3-3 3" stroke="#fff" stroke-width="1.6" fill="none"/></svg></a>
  </div>
  <div class="service" style="left:728px;top:441px">
    <div class="service-icon" style="background:var(--purple)"><svg width="16" height="20" viewBox="0 0 16 20"><path d="M1 1h9l5 5v13H1z" fill="none" stroke="#fff" stroke-width="2"/><path d="M4 15l3-4 2 2 3-3v5z" fill="#fff"/></svg></div>
    <h3>Quality digital photo prints</h3>
    <p>No matter the quantity of photocopies you need or the size of your<br>copy - you can rely on us to provide a top quality service!</p>
    <a href="#">Digital Photo Printing <svg width="12" height="12" viewBox="0 0 12 12"><circle cx="6" cy="6" r="6" fill="var(--link)"/><path d="m5 3 3 3-3 3" stroke="#fff" stroke-width="1.6" fill="none"/></svg></a>
  </div>
</section>

<h2 class="abs quote-title">GET A FREE QUOTE</h2>
<p class="abs quote-text">....or talk to our team about your requirements. Please fill out the form below and we will contact you within a day.  You can now upload and send us your file for a free quote.</p>
<div class="field" style="left:522px;top:2045px;width:279px">First name :</div>
<div class="field" style="left:814px;top:2045px;width:279px">Last name :</div>
<div class="field" style="left:522px;top:2094px;width:279px">Phone :</div>
<div class="field" style="left:814px;top:2094px;width:279px">Email :</div>
<div class="field" style="left:522px;top:2141px;width:279px;height:67px">Message :</div>
<div class="submit">SUBMIT NOW</div>

<footer class="site-footer"></footer>
<div class="partner-badge" style="top:2320px"><svg width="60" height="30"><rect width="60" height="30" rx="4" fill="#d3d3d3"/></svg></div>
<div class="partner-badge" style="top:2415px"><svg width="60" height="30"><rect width="60" height="30" rx="4" fill="#d3d3d3"/></svg></div>

<div class="footer-col" style="left:346px">
  <h4>WELCOME</h4>
  <ul><li>Home</li><li>About</li><li>Photocopying</li><li>Printing</li><li>Laminating</li><li>Business cards</li><li>Typing services</li></ul>
</div>
<div class="footer-col" style="left:501px;top:2344px">
  <ul><li>Film processing</li><li>Photo printing</li><li>Passport photos</li><li>&nbsp;Image restoration</li><li>Printer supplies</li></ul>
</div>
<div class="footer-col" style="left:712px">
  <h4>CONTACT</h4>
  <ul>
    <li>Inkvale</li>
    <li>120 Street name, City name,</li>
    <li>Country name.</li>
    <li class="contact-line" style="margin-top:4px"><svg width="9" height="12" viewBox="0 0 9 12"><rect x="1" y="0.5" width="7" height="11" rx="1.5" fill="none" stroke="#555"/><circle cx="4.5" cy="9.5" r=".8" fill="#555"/></svg>2365 555 018</li>
    <li class="contact-line" style="margin-top:4px"><svg width="11" height="10" viewBox="0 0 11 10"><rect x="3" y="0" width="5" height="3" fill="#555"/><rect x="0" y="3" width="11" height="4" rx="1" fill="#555"/><rect x="3" y="6" width="5" height="4" fill="#fff" stroke="#555"/></svg>2365 555 018</li>
    <li class="contact-line" style="margin-top:4px;text-transform:none"><svg width="11" height="8" viewBox="0 0 11 8"><rect width="11" height="8" fill="#555"/><path d="m0 0 5.5 4L11 0" stroke="#fff" fill="none"/></svg>info@inkvale.example</li>
  </ul>
</div>
<div class="footer-col social" style="left:982px">
  <h4>FOLLOW US</h4>
  <ul><li><span class="social-square"></span>: Friendline</li><li><span class="social-square"></span>: Chirper</li><li><span class="social-square"></span>: Linkwork</li><li><span class="social-square"></span>: Circles</li></ul>
</div>

<div class="bottom-bar">© 2015. INKVALE. ALL RIGHTS RESERVED.</div>

</body>
</html>
```